2 banners on the outside wall of the hall

Banner 1:
KalviMar specializes in the planning, construction, and maintenance of high-quality pond systems, particularly swimming ponds, natural pools, garden ponds, koi ponds, streams, and waterfalls. Learn more at www.kalvimar.de
The following data should be included:
Planning and construction of swimming ponds and natural pools, as well as garden ponds and koi ponds
100% organic
Individually planned
Over 20 years of experience
04627 3150962
www.kalvimar.de
“Logo-KalviMar”
Banner 2:
Grünflut-Laden is the online shop for high-quality aquatic plants for ponds and aquariums.
More information at https://gruenflut-laden.de
Online shop for pond plants and water lilies, as well as aquarium plants and accessories
Over 400 plant species
Top gardener quality
Secure packaging & fast shipping
04627 3150961
www.gruenflut-laden. de
“Logo Greenflow shop”
Here's roughly what we envision:
The designs for each banner should be clearly visible and include everything needed, without appearing cluttered. In other words, it should be immediately clear what the banner is about.
We should also be made aware of our unique selling points and advantages.
It is important that the banners also harmonize visually with each other.
We liked the banner image in the attachment and it serves as inspiration.
The banner print data is produced as follows:
• Banner size: Width x Height: 3880 mm x 1880 mm
• Material: Mesh banner, PVFormat: PDF (X-3:2000)
• Fonts: converted into paths
• Trim allowance: +2 mm all around
• Color space: CMYK
• Resolution: 72 dpi (recommended) at 1:1 resolution
Look and feel
Each slider illustrates characteristics of the customer's brand and the style your logo design should communicate.

```html
<!DOCTYPE html>
<html lang="de">
<head>
<meta charset="utf-8">
<title>KalviMar – Banner</title>
<link href="https://fonts.googleapis.com/css2?family=Rubik:wght@500;600;700&family=Quicksand:wght@500&family=Barlow:wght@600;700&display=swap" rel="stylesheet">
<style>
  :root {
    --brand-blue: #2c5f8a;
    --wave-mid: #7f9fbc;
    --wave-light: #d6e1ea;
    --white: #ffffff;
    --frame: #1a1a1a;
    --pool-green: #3fae8a;
    --garden-green: #6f8f4a;
    --sky-blue: #5d8fc4;
    --stone-grey: #9a9285;
  }
  * { margin: 0; padding: 0; box-sizing: border-box; }
  html, body { width: 1200px; height: 667px; overflow: hidden; background: var(--white); }
  .canvas { position: relative; width: 1200px; height: 667px; background: var(--white); }

  .size-label {
    position: absolute; right: 79px; top: 14px;
    font: 500 20px "Quicksand", sans-serif; color: var(--brand-blue);
  }
  .trim-frame {
    position: absolute; left: 83px; top: 83px; width: 1042px; height: 505px;
    border: 1px solid var(--frame);
  }
  .wave-band { position: absolute; left: 0; top: 0; width: 1200px; height: 667px; }

  .brand-name {
    position: absolute; left: 134px; top: 136px;
    font: 700 72px/1 "Rubik", sans-serif; color: var(--brand-blue);
    letter-spacing: -1px;
  }

  .headline {
    position: absolute; left: 505px; top: 128px;
    font: 600 31.5px/37px "Rubik", sans-serif; color: var(--white);
    white-space: nowrap;
  }

  .photo { position: absolute; width: 228px; height: 138px; }
  .photo--pool { left: 106px; top: 269px; border-bottom-right-radius: 40px;
    background: linear-gradient(180deg, var(--garden-green) 0%, #8aa36a 40%, var(--pool-green) 70%, #c9a883 100%); }
  .photo--meadow { left: 345px; top: 269px; border-bottom-left-radius: 40px;
    clip-path: polygon(0 0, 78% 0, 100% 34%, 100% 100%, 0 100%);
    background: linear-gradient(180deg, var(--sky-blue) 0%, #a9c4de 30%, #4f7a3a 55%, #6d8758 100%); }
  .photo--stream { left: 105px; top: 418px; border-top-right-radius: 40px;
    clip-path: polygon(0 0, 100% 0, 100% 100%, 19% 100%, 0 71%);
    background: linear-gradient(160deg, #5d7f3c 0%, var(--stone-grey) 45%, #b4a898 100%); }
  .photo--lake { left: 344px; top: 418px; border-top-left-radius: 40px;
    background: linear-gradient(180deg, #3f6a32 0%, #5f8a4a 35%, #6fa08a 60%, #8fb8b0 100%); }

  .benefits { position: absolute; left: 646px; top: 302px; list-style: none; }
  .benefits li {
    position: relative; padding-left: 34px; height: 43px;
    font: 500 32px/43px "Quicksand", sans-serif; color: var(--brand-blue);
    white-space: nowrap;
  }
  .benefits li::before {
    content: ""; position: absolute; left: 0; top: 16px;
    width: 14px; height: 14px; background: var(--brand-blue);
  }

  .phone { position: absolute; left: 646px; top: 459px; display: flex; align-items: center; gap: 20px; }
  .phone-icon { width: 49px; height: 40px; }
  .phone-number {
    font: 700 51px/1 "Barlow", sans-serif; color: var(--brand-blue); letter-spacing: 2.5px;
  }

  .web-band { position: absolute; left: 0; top: 0; width: 1200px; height: 667px; }
  .web { position: absolute; left: 674px; top: 540px; display: flex; align-items: center; gap: 18px; }
  .web-icon { width: 30px; height: 30px; }
  .web-url {
    font: 600 33px/1 "Barlow", sans-serif; color: var(--white); letter-spacing: 6.5px;
  }
</style>
</head>
<body>
<div class="canvas">
  <div class="size-label">3880mm x 1880mm</div>
  <div class="trim-frame"></div>

  <svg class="wave-band" viewBox="0 0 1200 667" aria-hidden="true">
    <path fill="var(--wave-light)" d="M466 99 H1140 V277 C1000 250 880 262 760 278 C640 292 540 287 452 228 Z"/>
    <path fill="var(--wave-mid)" d="M466 99 H1140 V255 C1000 232 880 245 760 266 C640 284 540 281 452 228 Z"/>
    <path fill="var(--brand-blue)" d="M466 99 H1140 V235 C1000 220 880 232 760 255 C640 276 540 272 452 228 Z"/>
  </svg>

  <div class="brand-name">KalviMar</div>

  <h1 class="headline">Planung und Bau von Schwimmteichen<br>und Naturpools sowie Gartenteichen<br>und Koiteichen</h1>

  <div class="photo photo--pool" role="img" aria-label="Foto: Naturpool mit Holzdeck im Garten"></div>
  <div class="photo photo--meadow" role="img" aria-label="Foto: Schwimmteich mit Steg in naturnaher Landschaft"></div>
  <div class="photo photo--stream" role="img" aria-label="Foto: Bachlauf mit Steinen und Wasserfall"></div>
  <div class="photo photo--lake" role="img" aria-label="Foto: Schwimmteich mit Seerosen und Sonnendeck"></div>

  <ul class="benefits">
    <li>100% biologisch</li>
    <li>Individuell geplant</li>
    <li>Über 20 Jahre Erfahrung</li>
  </ul>

  <div class="phone">
    <svg class="phone-icon" viewBox="0 0 49 40" aria-hidden="true">
      <path fill="var(--brand-blue)" d="M2 12 C2 2 47 2 47 12 V16 H36 V10 H13 V16 H2 Z"/>
      <path fill="var(--brand-blue)" d="M14 14 H35 L44 30 V38 H5 V30 Z"/>
      <g fill="var(--white)">
        <rect x="19" y="21" width="3" height="3"/><rect x="23" y="21" width="3" height="3"/><rect x="27" y="21" width="3" height="3"/>
        <rect x="19" y="25" width="3" height="3"/><rect x="23" y="25" width="3" height="3"/><rect x="27" y="25" width="3" height="3"/>
        <rect x="19" y="29" width="3" height="3"/><rect x="23" y="29" width="3" height="3"/><rect x="27" y="29" width="3" height="3"/>
      </g>
    </svg>
    <span class="phone-number">04627 3150962</span>
  </div>

  <svg class="web-band" viewBox="0 0 1200 667" aria-hidden="true">
    <polygon fill="var(--brand-blue)" points="647,522 1140,522 1140,604 591,604"/>
  </svg>
  <div class="web">
    <svg class="web-icon" viewBox="0 0 30 30" aria-hidden="true">
      <g fill="none" stroke="var(--white)" stroke-width="2">
        <circle cx="15" cy="15" r="13"/>
        <ellipse cx="15" cy="15" rx="6" ry="13"/>
        <line x1="15" y1="2" x2="15" y2="28"/>
        <line x1="2" y1="15" x2="28" y2="15"/>
        <path d="M4.5 8.5 H25.5 M4.5 21.5 H25.5"/>
      </g>
    </svg>
    <span class="web-url">www.kalvimar.de</span>
  </div>
</div>
</body>
</html>
```